KBT Business Cards

We require business cards for our business. We would like a matte black back to the card, with our logo centred in the middle. The front side of the card is open to design.

Target Market(s)

Clients looking for legal services (professional)

Industry/Entity Type

Legal

Contact Information for Business Card

Doran Kelbrath
Partner
Mobile: 0461 738 524
Email: doran@kbtlaw.co
Website: www.kbtlaw.co
Level 3, 118 Wendmore Street
Sydney NSW 2000

Font styles to use
Other font styles liked:
• Avenir

Colors
f04a50
ffffff
1b1b1b

Requirements
Must have
• Black back with logo included in the centre of the card.
• Our font is Avenir.

```html
<!DOCTYPE html>
<html lang="en">
<head>
<meta charset="utf-8">
<title>KBT Business Card</title>
<link rel="stylesheet" href="https://fonts.googleapis.com/css2?family=Nunito+Sans:wght@400;600;700;800&display=swap">
<style>
  :root {
    --stage: #2c2c30;
    --card: #1b1b1b;
    --accent: #c8234a;
    --white: #ffffff;
    --gloss: #6e6e72;
    --muted: #d8d8d8;
  }
  * { margin: 0; padding: 0; box-sizing: border-box; }
  html, body {
    width: 1200px; height: 800px; overflow: hidden;
    background: var(--stage);
    font-family: "Nunito Sans", "Avenir", sans-serif;
  }
  .stage {
    width: 1200px; height: 800px;
    display: flex; align-items: center; justify-content: center; gap: 40px;
  }
  .card {
    position: relative;
    width: 540px; height: 330px;
    background: var(--card);
    border-radius: 18px;
    box-shadow: 0 18px 40px rgba(0,0,0,.45);
    overflow: hidden;
  }

  /* Back side */
  .card-back {
    display: flex; flex-direction: column; align-items: center; justify-content: center;
  }
  .back-brand { display: flex; align-items: center; gap: 18px; }
  .brand-square { width: 46px; height: 46px; background: #0c0c0c; }
  .back-wordmark {
    color: var(--gloss);
    font-weight: 700; font-size: 26px; line-height: 1.0;
    letter-spacing: .5px; text-transform: uppercase;
  }
  .back-web {
    margin-top: 34px;
    color: var(--muted);
    font-size: 12px; letter-spacing: 3px;
  }

  /* Front side */
  .card-front { padding: 40px 44px; }
  .front-wordmark {
    color: var(--white);
    font-weight: 800; font-size: 34px; line-height: .98;
    text-transform: uppercase; letter-spacing: .3px;
  }
  .person { margin-top: 26px; }
  .person-name {
    color: var(--accent);
    font-weight: 700; font-size: 15px; text-transform: uppercase; letter-spacing: .5px;
  }
  .person-role { color: var(--white); font-size: 13px; }
  .address { margin-top: 14px; color: var(--white); font-size: 13px; line-height: 1.45; }
  .contacts { margin-top: 8px; list-style: none; }
  .contact {
    display: flex; align-items: center; gap: 10px;
    color: var(--white); font-size: 13px; line-height: 1.6;
  }
  .contact svg { width: 12px; height: 12px; flex: none; }
</style>
</head>
<body>
<main class="stage">
  <section class="card card-back" aria-label="Card back">
    <div class="back-brand">
      <span class="brand-square"></span>
      <div class="back-wordmark">Kelbrath<br>Bryce<br>Thorne</div>
    </div>
    <p class="back-web">www.kbtlaw.co</p>
  </section>

  <section class="card card-front" aria-label="Card front">
    <div class="front-wordmark">Kelbrath<br>Bryce<br>Thorne</div>
    <div class="person">
      <p class="person-name">Doran Kelbrath</p>
      <p class="person-role">Partner</p>
    </div>
    <p class="address">Level 3, 118 Wendmore Street<br>Sydney NSW 2000</p>
    <ul class="contacts">
      <li class="contact">
        <svg viewBox="0 0 12 12" aria-hidden="true"><rect x="3" y="1" width="6" height="10" rx="1" fill="none" stroke="var(--accent)" stroke-width="1.4"/></svg>
        0461 738 524
      </li>
      <li class="contact">
        <svg viewBox="0 0 12 12" aria-hidden="true"><rect x="1" y="2.5" width="10" height="7" fill="var(--accent)"/><path d="M1 2.5 6 6.5 11 2.5" fill="none" stroke="var(--card)" stroke-width="1"/></svg>
        doran@kbtlaw.co
      </li>
      <li class="contact">
        <svg viewBox="0 0 12 12" aria-hidden="true"><circle cx="6" cy="6" r="5" fill="var(--accent)"/><path d="M1 6h10M6 1c-2 2.5-2 7.5 0 10M6 1c2 2.5 2 7.5 0 10" fill="none" stroke="var(--card)" stroke-width=".8"/></svg>
        www.kbtlaw.co
      </li>
    </ul>
  </section>
</main>
</body>
</html>
```